Design a compelling Tarnwove Business Card that will drive people to my site

I want a business card that I can give to people—less to tell them who I am and more to direct them to my website. My website is a portal for Pelmor Aquatics Officials and a place for people who want to become Pelmor Aquatics Officials.
I am uploading my official company logo as well as a business card mockup that I did on my own. Please feel free to completely stray from this design.
I've included a screen recording of the homepage of my website as well.
Target Market(s)
Pelmor Aquatics Officials and people who desire to become one
Contact Information for Business Card
website url
Look and feel
Each slider illustrates characteristics of the customer's brand and the style your logo design should communicate.

```html
<!DOCTYPE html>
<html lang="en">
<head>
<meta charset="utf-8">
<title>Tarnwove Business Card</title>
<link href="https://fonts.googleapis.com/css2?family=Montserrat:wght@700;800&family=Roboto:wght@400&display=swap" rel="stylesheet">
<style>
  :root {
    --navy: #2b4185;
    --navy-deep: #1f3272;
    --navy-dark: #354684;
    --sky: #8fa9dc;
    --brand: #3550a8;
    --white: #ffffff;
    --ink: #2a2f45;
    --stage: #e9ebf0;
  }
  * { margin: 0; padding: 0; box-sizing: border-box; }
  html, body { width: 1200px; height: 880px; overflow: hidden; }
  body {
    background: var(--stage);
    font-family: "Roboto", Arial, sans-serif;
    position: relative;
  }
  .card {
    position: absolute;
    left: 300px;
    width: 600px;
    height: 343px;
    border-radius: 22px;
    overflow: hidden;
    box-shadow: 0 8px 24px rgba(20, 30, 60, 0.18);
  }
  .card-back { top: 70px; background: var(--navy); }
  .card-front { top: 467px; background: var(--white); }

  .back-name {
    position: absolute;
    left: 0; right: 0; top: 100px;
    text-align: center;
    font-family: "Montserrat", Arial, sans-serif;
    font-weight: 800;
    font-size: 80px;
    line-height: 1;
    letter-spacing: -1px;
    color: var(--navy-deep);
  }
  .tagline {
    position: absolute;
    left: 0; right: 0; top: 222px;
    text-align: center;
    font-family: "Montserrat", Arial, sans-serif;
    font-weight: 800;
    font-size: 24px;
    line-height: 1.2;
    color: var(--white);
  }

  .wave { position: absolute; inset: 0; width: 600px; height: 343px; }
  .identity {
    position: absolute;
    right: 48px; top: 36px;
    text-align: right;
  }
  .identity-name {
    font-family: "Montserrat", Arial, sans-serif;
    font-weight: 800;
    font-size: 24px;
    line-height: 1.2;
    color: var(--brand);
  }
  .identity-role {
    font-size: 15px;
    color: var(--ink);
    margin-top: 2px;
  }
  .edge-bar {
    position: absolute;
    right: 0; top: 30px;
    width: 16px; height: 34px;
    background: var(--navy-dark);
  }
  .front-name {
    position: absolute;
    left: 40px; top: 118px;
    font-family: "Montserrat", Arial, sans-serif;
    font-weight: 800;
    font-size: 54px;
    line-height: 1;
    letter-spacing: -1px;
    color: var(--brand);
  }
  .contact {
    position: absolute;
    right: 30px; top: 206px;
    list-style: none;
    color: var(--white);
    font-size: 17px;
    line-height: 30px;
    text-align: right;
  }
  .contact li { display: flex; align-items: center; justify-content: flex-end; gap: 10px; }
  .contact svg { width: 16px; height: 16px; }
  .icon-phone { fill: var(--white); }
  .icon-mail { fill: none; stroke: var(--white); stroke-width: 2; stroke-linejoin: round; }
</style>
</head>
<body>
  <section class="card card-back">
    <div class="back-name">Tarnwove</div>
    <div class="tagline">The Deck Judge's Open Gateway</div>
  </section>

  <section class="card card-front">
    <svg class="wave" viewBox="0 0 600 343" aria-hidden="true">
      <path fill="var(--sky)" d="M0,282 C150,316 255,284 352,176 C424,96 490,76 600,76 L600,343 L0,343 Z"/>
      <path fill="var(--white)" d="M0,296 C150,328 262,298 362,190 C432,112 494,94 600,94 L600,343 L0,343 Z"/>
      <path fill="var(--navy-dark)" d="M0,302 C150,334 266,304 366,196 C436,118 496,100 600,100 L600,343 L0,343 Z"/>
    </svg>
    <div class="edge-bar"></div>
    <div class="identity">
      <div class="identity-name">Marcus Ellery</div>
      <div class="identity-role">CEO &amp; Founder</div>
    </div>
    <div class="front-name">Tarnwove</div>
    <ul class="contact">
      <li>(555) 271-0438
        <svg class="icon-phone" viewBox="0 0 24 24"><path d="M6.6 10.8a15.1 15.1 0 0 0 6.6 6.6l2.2-2.2a1 1 0 0 1 1-.25 11.4 11.4 0 0 0 3.6.57 1 1 0 0 1 1 1V20a1 1 0 0 1-1 1A17 17 0 0 1 3 4a1 1 0 0 1 1-1h3.5a1 1 0 0 1 1 1c0 1.25.2 2.45.57 3.6a1 1 0 0 1-.25 1z"/></svg>
      </li>
      <li>marcus@tarnwove.com
        <svg class="icon-mail" viewBox="0 0 24 24"><rect x="3" y="6" width="18" height="12"/><path d="M3 6l9 7 9-7"/></svg>
      </li>
    </ul>
  </section>
</body>
</html>
```